Web Design

We need a website for a company based in Doha Qatar called
Lumara Maid Service.

It is the number one maid cleaning service company, and we have branches all over qatar.

Luxury Cleaning Service Provider.

The color scheme is gold, yellow and black like the logo.

Before they get to the website, there is an intro video.

The website should depict luxury.

Target Market(s)

People who need maids at their houses.

Industry/Entity Type

Cleaning Service

Requirements
Must have
• Luxury, Sleek, Modern

The opening sequence is a video which I already have. Its too big to upload here so I am going to put it on youtube.

After the opening sequence, the home page should have a widescreen photo background and it should change every five seconds, the first background photo should be of qatar westbay skyline. Then the second background should be of maid photos in cleaning positions. Then the third background should be of cleaner photos etc.

We will send you all the tabs and all the content later.

```html
<!DOCTYPE html>
<html lang="en">
<head>
<meta charset="utf-8">
<title>Lumara Maid Service — Cleaning Company in Qatar</title>
<link href="https://fonts.googleapis.com/css2?family=Oswald:wght@400;500&family=Open+Sans:wght@400;600&display=swap" rel="stylesheet">
<style>
  :root {
    --black: #000000;
    --gold: #fcbb48;
    --gold-text: #f7b436;
    --white: #ffffff;
    --ink: #0b0b0b;
    --control-bg: #e4e4e4;
    --control-dark: #5c5c5c;
    --progress: #e8403f;
    --photo-light: #e9ebe6;
    --photo-mid: #c9d0c4;
  }
  * { box-sizing: border-box; margin: 0; padding: 0; }
  html, body { width: 1200px; height: 675px; overflow: hidden; background: var(--black); }
  body { font-family: "Open Sans", Arial, sans-serif; position: relative; }

  .site-header { position: absolute; left: 0; top: 0; width: 1200px; height: 126px; background: var(--black); }
  .brand { position: absolute; left: 180px; top: 44px; display: flex; align-items: center; gap: 12px; }
  .brand-mark { width: 34px; height: 34px; border-radius: 50%; background: var(--gold-text); }
  .brand-name { font-family: "Open Sans", Arial, sans-serif; font-size: 20px; font-weight: 600; color: var(--gold-text); letter-spacing: 0.3px; }

  .search { position: absolute; left: 871px; top: 27px; width: 149px; height: 41px; background: var(--white); display: flex; align-items: center; padding-left: 12px; gap: 9px; }
  .search-label { font-size: 12px; color: #b3b3b3; }

  .main-nav { position: absolute; top: 91px; right: 180px; display: flex; gap: 56px; }
  .main-nav a, .footer-nav a { color: var(--gold-text); text-decoration: none; font-size: 12.5px; }

  .hero { position: absolute; left: 0; top: 126px; width: 1200px; height: 438px; background: var(--gold); }
  .hero-copy { position: absolute; left: 180px; top: 72px; font-family: "Oswald", "Arial Narrow", sans-serif; }
  .hero-intro { font-size: 31px; font-weight: 500; color: var(--white); line-height: 1; letter-spacing: -0.3px; }
  .hero-title { font-size: 78px; font-weight: 500; color: var(--ink); line-height: 81px; margin-top: 12px; letter-spacing: -0.5px; }
  .hero-place { font-size: 26px; font-weight: 500; color: var(--white); line-height: 1; margin-top: 12px; letter-spacing: -0.3px; }
  .hero-note { font-family: "Open Sans", Arial, sans-serif; font-size: 19px; color: var(--ink); margin-top: 5px; padding-left: 5px; }

  .video-player { position: absolute; left: 540px; top: 51px; width: 480px; height: 320px; box-shadow: 0 2px 8px rgba(0,0,0,0.25); }
  .video-frame { width: 480px; height: 291px; background: linear-gradient(180deg, var(--photo-mid) 0%, var(--photo-light) 55%, #f3f3f1 100%); }
  .video-controls { height: 29px; background: linear-gradient(180deg, #f1f1f1, var(--control-bg)); display: flex; align-items: center; padding: 0 10px; gap: 10px; font-size: 9px; color: #444; }
  .control-divider { width: 1px; height: 17px; background: #c4c4c4; }
  .progress { position: relative; width: 240px; height: 8px; border-radius: 4px; background: var(--control-dark); }
  .progress-buffer { position: absolute; left: 0; top: 0; width: 162px; height: 8px; border-radius: 4px; background: #7b7b7b; }
  .progress-played { position: absolute; left: 0; top: 0; width: 117px; height: 8px; border-radius: 4px; background: var(--progress); }
  .progress-knob { position: absolute; left: 110px; top: -2px; width: 12px; height: 12px; border-radius: 50%; background: #e6e6e6; border: 1px solid #999; }
  .volume { position: relative; width: 60px; height: 6px; border-radius: 3px; background: var(--control-dark); }
  .volume-knob { position: absolute; right: 0; top: -2px; width: 9px; height: 9px; border-radius: 50%; background: #eee; border: 1px solid #888; }

  .site-footer { position: absolute; left: 0; top: 564px; width: 1200px; height: 111px; background: var(--black); }
  .footer-nav { position: absolute; left: 180px; top: 30px; display: flex; gap: 56px; }
  .copyright { position: absolute; left: 180px; top: 57px; font-size: 12.5px; color: var(--gold-text); }
  .social { position: absolute; left: 895px; top: 38px; display: flex; gap: 1px; }
  .social span { width: 31px; height: 31px; border-radius: 50%; background: var(--white); }
</style>
</head>
<body>
  <header class="site-header">
    <div class="brand">
      <span class="brand-mark"></span>
      <span class="brand-name">Lumara Maid Service</span>
    </div>
    <div class="search">
      <svg width="12" height="12" viewBox="0 0 12 12" aria-hidden="true">
        <circle cx="5" cy="5" r="3.6" fill="none" stroke="#9a9a9a" stroke-width="1.8"/>
        <line x1="7.6" y1="7.6" x2="11" y2="11" stroke="#9a9a9a" stroke-width="2"/>
      </svg>
      <span class="search-label">Search</span>
    </div>
    <nav class="main-nav">
      <a href="#">Home</a><a href="#">About us</a><a href="#">Services</a><a href="#">Recent News</a><a href="#">Contact</a>
    </nav>
  </header>

  <main class="hero">
    <div class="hero-copy">
      <p class="hero-intro">We are a very famous</p>
      <h1 class="hero-title">Cleaning<br>Company</h1>
      <p class="hero-place">in Qatar</p>
      <p class="hero-note">and have branches all over</p>
    </div>

    <div class="video-player">
      <div class="video-frame" role="img" aria-label="Video still of staff cleaning and vacuuming a bright tiled lobby"></div>
      <div class="video-controls">
        <svg width="14" height="14" viewBox="0 0 14 14" aria-hidden="true"><path d="M2 1 L13 7 L2 13 Z" fill="#6a6a6a"/></svg>
        <span class="control-divider"></span>
        <div class="progress"><span class="progress-buffer"></span><span class="progress-played"></span><span class="progress-knob"></span></div>
        <span>3.47 / 9.29</span>
        <span class="control-divider"></span>
        <svg width="16" height="14" viewBox="0 0 16 14" aria-hidden="true"><path d="M1 5 H4 L8 1 V13 L4 9 H1 Z" fill="#555"/><path d="M10 4 Q12 7 10 10 M12 2 Q15 7 12 12" stroke="#555" fill="none" stroke-width="1.2"/></svg>
        <div class="volume"><span class="volume-knob"></span></div>
        <span class="control-divider"></span>
        <svg width="13" height="13" viewBox="0 0 13 13" aria-hidden="true"><path d="M1 4 V1 H4 M9 1 H12 V4 M12 9 V12 H9 M4 12 H1 V9" stroke="#555" fill="none" stroke-width="1.4"/><rect x="4" y="4" width="5" height="5" fill="#555"/></svg>
      </div>
    </div>
  </main>

  <footer class="site-footer">
    <nav class="footer-nav">
      <a href="#">Home</a><a href="#">About us</a><a href="#">Services</a><a href="#">Recent News</a><a href="#">Contact</a>
    </nav>
    <p class="copyright">© 2014 Lumara Maid Service. All Rights Reserved</p>
    <div class="social" aria-label="Social links"><span></span><span></span><span></span><span></span></div>
  </footer>
</body>
</html>
```